Envelope design

We need a envelope design for a professional services firm called Brenwick Tax Advisory Inc. The firm is essentially a very specialized tax accounting firm - instead of serving the end consumer, we support other public accounting firms in the area of Canadian and U.S. tax advisory and compliance (i.e. they call us on tax issues too complex for the general practitioner). Our byline is "Tax Support Services for Public Accounting Firms". Our postcard should utilize our logo and be based on colours present in our logo (see file attached). The final design needs to convey professionalism and trustworthiness (we're hired by accountants after all!) while being creative and eye-catching. Eye-catching is critical, since many prospective recipients will not have heard from me before and I want them to read the postcard.
At lot of design work has already been done here. I've attached a number of sample files showing logo and letterhead designs. Please note that the letterhead hasn't yet been updated for the new logo. This is happening in a separate design competition.
Updates
Project Deadline Extended Reason: Deadline is extended because I am pricing the extra cost of having colour right to the edge of the envelopes. This will help me design on final design. Pricing should come in on Monday. Added Saturday, February 20, 2016

```html
<!DOCTYPE html>
<html lang="en">
<head>
<meta charset="utf-8">
<title>Brenwick Tax Advisory – Envelope Options</title>
<link rel="stylesheet" href="https://fonts.googleapis.com/css2?family=Open+Sans:wght@400;600;700&display=swap">
<style>
  :root {
    --paper: #ffffff;
    --ink: #231f20;
    --ink-soft: #5a5a5a;
    --accent-red: #e94e2a;
    --accent-orange: #f5a623;
    --gold: #f7b21d;
    --band-black: #231f20;
    --band-navy: #1c2f5c;
    --window: #9b9b9b;
    --mark-blue: #1f5fa8;
  }
  * { margin: 0; padding: 0; box-sizing: border-box; }
  html, body { width: 1200px; height: 1164px; overflow: hidden; }
  body {
    position: relative;
    background: radial-gradient(ellipse at 50% 50%, #ffffff 0%, #eeeeee 70%, #e2e2e2 100%);
    font-family: "Open Sans", Arial, sans-serif;
  }
  .option-number {
    position: absolute;
    left: 37px;
    font: 700 42px/1 "Open Sans", Arial, sans-serif;
    color: #111;
  }
  .envelope {
    position: absolute;
    left: 92px;
    width: 1066px;
    height: 505px;
    background: var(--paper);
    box-shadow: 6px 8px 14px rgba(0,0,0,0.35);
    overflow: hidden;
  }
  .envelope--contact { top: 55px; }
  .envelope--window { top: 618px; }
  .brand { position: absolute; left: 44px; top: 77px; }
  .brand__mark {
    position: absolute; left: 0; top: 0;
    width: 54px; height: 54px;
    background: var(--mark-blue);
  }
  .brand__name {
    position: absolute; left: 68px; top: -2px;
    font: 700 31px/1.1 "Open Sans", Arial, sans-serif;
    color: var(--ink);
    white-space: nowrap;
  }
  .brand__tagline {
    position: absolute; left: 69px; top: 38px;
    font: 400 15px/1 "Open Sans", Arial, sans-serif;
    color: var(--ink-soft);
    white-space: nowrap;
  }
  .contact {
    position: absolute; left: 43px; top: 334px;
    list-style: none;
    font-size: 16px; font-weight: 600; line-height: 23px;
    color: #3a3a3a;
  }
  .contact__label { color: var(--accent-red); font-weight: 700; }
  .accent-stripe {
    position: absolute; left: 0; width: 100%; height: 11px;
    background: linear-gradient(90deg, var(--accent-red) 0%, var(--accent-orange) 100%);
  }
  .footer-band { position: absolute; left: 0; bottom: 0; width: 100%; }
  .envelope--contact .accent-stripe { top: 426px; }
  .envelope--contact .footer-band { top: 437px; background: var(--band-black); }
  .envelope--window .accent-stripe { top: 424px; }
  .envelope--window .footer-band { top: 434px; background: var(--band-navy); }
  .website {
    position: absolute; right: 120px; bottom: 18px;
    font-size: 17px; font-weight: 700;
    color: var(--gold);
  }
  .address-window {
    position: absolute; left: 46px; top: 327px;
    width: 508px; height: 129px;
    border-radius: 8px;
    background: var(--window);
    z-index: 2;
  }
</style>
</head>
<body>
  <div class="option-number" style="top:136px;">8</div>
  <section class="envelope envelope--contact">
    <div class="brand">
      <span class="brand__mark"></span>
      <div class="brand__name">Brenwick Tax Advisory</div>
      <div class="brand__tagline">Tax Support for Public Accounting Firms</div>
    </div>
    <ul class="contact">
      <li><span class="contact__label">P</span> : 902.555.0148</li>
      <li><span class="contact__label">F</span> : 902.555.0193</li>
      <li><span class="contact__label">E</span> : alan@brenwicktax.com</li>
    </ul>
    <div class="accent-stripe"></div>
    <div class="footer-band">
      <span class="website">www.BrenwickTax.com</span>
    </div>
  </section>

  <div class="option-number" style="top:684px;">9</div>
  <section class="envelope envelope--window">
    <div class="brand">
      <span class="brand__mark"></span>
      <div class="brand__name">Brenwick Tax Advisory</div>
      <div class="brand__tagline">Tax Support for Public Accounting Firms</div>
    </div>
    <div class="address-window" role="img" aria-label="Address window"></div>
    <div class="accent-stripe"></div>
    <div class="footer-band">
      <span class="website">www.BrenwickTax.com</span>
    </div>
  </section>
</body>
</html>
```